Elegant Business Card for Technology Company

Client is a supplier of innovative industrial communications and automation equipment since 2002. This contest is to gather fresh ideas for a redesign of the existing business card. Client is looking for design that best communicates tagline "Industrial Networking and Computing Specialist".

Design submissions should look modern, clean, elegant and professional. It should not be cluttered. Use white as the primary colour. Orange and black as secondary colour. Refer to jpeg File 1 on the current design.

Fonts used by Client used include Arial Regular, Arial Black, Roboto Regular, Roboto Black and Lato.

The winning design will be sent for offset printing using super white 250gsm artcard paper (open for suggestions).

Target Market(s)

System Engineers, Project Managers, Purchasing Managers from companies providing engineering services for Smart Cities.

Industry/Entity Type

Information Technology

Contact Information for Business Card

Refer to PDF File 3 for Business Card Details. Priority of short contact information would be as follows Name > Job Title > Email > Mobile > Web > Tel > Fax > Business Address >UEN (UEN represents company registration number)

Font styles to use
Sans Serif

Colors
ffffff
f37122
000000
5c5c5c

Requirements
Must have
• Refer to AI File 2 (Company Logo) & PDF File 3 (Information on Namecard)
Should not have
• No QR codes
• No Social Media Icons
• Do not create full Black or Orange colour background

```html
<!DOCTYPE html>
<html lang="en">
<head>
<meta charset="utf-8">
<title>Korvan Business Card</title>
<link href="https://fonts.googleapis.com/css2?family=Lato:wght@400;700;900&display=swap" rel="stylesheet">
<style>
  :root {
    --white: #ffffff;
    --orange: #f37122;
    --black: #000000;
    --grey: #5c5c5c;
    --stage: #e6e4e0;
  }
  * { margin: 0; padding: 0; box-sizing: border-box; }
  html, body { width: 1200px; height: 780px; overflow: hidden; }
  body { background: var(--stage); font-family: "Lato", Arial, sans-serif; position: relative; }

  .card {
    position: absolute; width: 560px; height: 320px;
    background: var(--white); overflow: hidden;
    box-shadow: 0 6px 18px rgba(0,0,0,0.18);
  }
  .card--front { left: 40px; top: 50px; }
  .card--back { left: 600px; top: 410px; }

  .dot-field {
    position: absolute; border-radius: 50%;
    background: radial-gradient(circle, rgba(243,113,34,0.07) 0%, rgba(243,113,34,0) 70%);
  }
  .card--front .dot-field { left: 250px; top: -40px; width: 300px; height: 220px; }
  .card--back .dot-field { left: 40px; top: 170px; width: 300px; height: 200px; }

  .shape-layer { position: absolute; inset: 0; }

  .brand { position: absolute; display: flex; align-items: center; gap: 10px; }
  .brand__dot { width: 62px; height: 62px; border-radius: 50%; background: var(--orange); }
  .brand__name { font-weight: 900; font-size: 42px; color: var(--black); letter-spacing: 1px; line-height: 1; }

  .card--front .brand { left: 28px; top: 148px; }
  .company-line { position: absolute; left: 28px; top: 220px; font-size: 14px; color: var(--black); white-space: nowrap; }

  .person { position: absolute; left: 262px; top: 124px; }
  .person__name { font-size: 22px; font-weight: 700; color: var(--black); line-height: 1.1; }
  .person__title { font-size: 14px; color: var(--orange); margin-bottom: 8px; }
  .contact-list { list-style: none; }
  .contact-list li { display: flex; align-items: center; gap: 8px; font-size: 12.5px; color: var(--black); line-height: 18px; white-space: nowrap; }
  .contact-list svg { width: 13px; height: 13px; flex: none; }

  .address { position: absolute; right: 24px; top: 26px; text-align: right; font-size: 13px; color: var(--black); line-height: 19px; }
  .address__uen-label { color: var(--orange); }

  .web-strip {
    position: absolute; left: 0; top: 0; width: 34px; height: 320px; background: var(--black);
  }
  .web-strip__text {
    position: absolute; left: 17px; top: 70px; transform: translate(-50%, 0) rotate(-90deg);
    transform-origin: center; color: var(--orange); font-size: 13px; white-space: nowrap;
  }
  .card--back .brand { left: 70px; top: 26px; }
  .tagline { position: absolute; left: 70px; top: 108px; font-size: 17px; font-weight: 700; color: var(--black); }
  .service-list { position: absolute; left: 70px; top: 140px; list-style: none; }
  .service-list li { display: flex; align-items: center; gap: 10px; font-size: 13.5px; color: var(--grey); line-height: 21px; }
  .service-list li::before { content: ""; width: 7px; height: 7px; border-radius: 50%; background: var(--orange); flex: none; }
  .link-marks { position: absolute; left: 70px; bottom: 22px; display: flex; gap: 8px; }
  .link-marks span { width: 20px; height: 20px; border-radius: 3px; background: var(--grey); opacity: 0.55; }
  .back-company { position: absolute; right: 26px; bottom: 22px; font-size: 15px; color: var(--black); }
</style>
</head>
<body>

<section class="card card--front" aria-label="Business card front">
  <div class="dot-field" role="img" aria-label="Faint orange dot pattern"></div>
  <svg class="shape-layer" viewBox="0 0 560 320" aria-hidden="true">
    <polygon points="0,246 560,294 560,301 0,253" fill="var(--orange)"/>
    <polygon points="0,253 560,301 560,320 0,320" fill="var(--black)"/>
  </svg>
  <div class="brand"><span class="brand__dot"></span><span class="brand__name">KVR</span></div>
  <div class="company-line">Korvan Asia Pacific Pte Ltd</div>

  <div class="address">
    <div><span class="address__uen-label">UEN No</span> 200309117</div>
    <div>25 Harlow Crescent Harlow Techpark</div>
    <div>#02-15 (Lobby B), Singapore 401234</div>
  </div>

  <div class="person">
    <div class="person__name">Daniel Lowe</div>
    <div class="person__title">Sales Manager</div>
    <ul class="contact-list">
      <li><svg viewBox="0 0 13 13"><rect width="13" height="13" fill="var(--orange)"/><rect x="4" y="2" width="5" height="9" rx="1" fill="none" stroke="#fff" stroke-width="1.2"/></svg>+65 8123 4567</li>
      <li><svg viewBox="0 0 13 13"><rect width="13" height="13" fill="var(--orange)"/><path d="M3 4 Q4 3 5 4 L5.5 5.5 L4.8 6.2 Q5.8 7.8 6.8 8.2 L7.5 7.5 L9 8 Q10 9 9 10 Q6 10.5 3 7 Q2.5 5 3 4Z" fill="#fff"/></svg>+65 6300 1122</li>
      <li><svg viewBox="0 0 13 13"><rect width="13" height="13" fill="var(--orange)"/><rect x="3" y="5" width="7" height="5" fill="#fff"/><rect x="4" y="2.5" width="5" height="3" fill="none" stroke="#fff" stroke-width="1"/></svg>+65 6300 1133</li>
      <li><svg viewBox="0 0 13 13"><rect width="13" height="13" fill="var(--orange)"/><rect x="2.5" y="4" width="8" height="5.5" fill="none" stroke="#fff" stroke-width="1"/><path d="M2.5 4 L6.5 7 L10.5 4" fill="none" stroke="#fff" stroke-width="1"/></svg>sales@korvan.com.sg</li>
    </ul>
  </div>
</section>

<section class="card card--back" aria-label="Business card back">
  <div class="dot-field" role="img" aria-label="Faint dot pattern"></div>
  <div class="web-strip"><span class="web-strip__text">korvan.com</span></div>
  <div class="brand"><span class="brand__dot"></span><span class="brand__name">KVR</span></div>
  <div class="tagline">Industrial Networking and Computing Specialist</div>
  <ul class="service-list">
    <li>Industrial Ethernet / Wireless / Cellular</li>
    <li>Industrial and Embedded Computing</li>
    <li>Serial / Fieldbus Connectivity</li>
    <li>IP Video Surveillance</li>
    <li>Remote Automation</li>
  </ul>
  <div class="link-marks" aria-hidden="true"><span></span><span></span><span></span></div>
  <div class="back-company">Korvan Asia Pacific Pte Ltd</div>
</section>

</body>
</html>
```